2-Page Flyer for the Information Session about the Quiet Pathfinder Course

This is a flyer to announce/advertise an evening Information Session about the Quiet Pathfinder Course. This Program aims at mindfully rethinking and redesigning work (and life) for people who feel stuck or not entirely satisfied with their work and/or life (please see draft flyer attached for more details). This Program is property of Bright Meadow, a company that uses a combination of Mindfulness, Design, and Entrepreneurship to help people achieve greater happiness (in their work and lives).

Target Market(s)

People who feel stuck or not entirely satisfied with their work and/or life (please see draft flyer attached for more details)

Font styles to use
Serif
Sans Serif

Colors
ffffff
f37122
33a6d7
acd037

Requirements
Must have
• All of what I will say below is suggestive (I’m not a design expert), and I’m open to divert from it, if it makes sense and feels more interesting.
• I thought initially of a 2-page flyer (please see draft flyer attached). The first page could help people grasp the essence of the event quickly (in 1 or 2 minutes), and then, if they are interested/motivated, they would continue reading through page 2, which has more info about the Program in itself.
• Potential Structure
• Page 1
• . About the Information Session on the Quiet Pathfinder Course
• . Visible Date & Time, Contacts, Venue (and other relevant info)
• . About me (the facilitator)
• Page 2
• . About the Quiet Pathfinder Course
• I include a Powerpoint draft of the flyer with the content. The design is rudimentary and precarious from an aesthetics/organization point of view, and this is mainly where I need help (and maybe in other aspects too!).
• On the flyer, I would like to include:
• . A photo of myself (I attach 1 picture).
• . 1 or 2 beautiful-nature photos (cropped or full). One may have to do with looking at the sky, dreaming, and imagining a new work and life (2 photos with sky and clouds attached). The other has to do with walking the transformation journey (the photo with the person walking through the forest path).
• . bright meadow logo or logos (there are two slightly different ones, that can be used for different purposes). For the first page, I would like the bright meadow logo that has "bright meadow" written on the bottom, with the saying "Stillness, Craft and Venture for Bright Meadow" beneath. This is the main logo. For the 2nd page, you can choose the logo that adapts better.
• - Where it says the "the way out is in" it would be great to have a similar font to the one I attach (see file "Font_the_way_out_is_in.png" and Ankecallig-fg.ttf
Nice to have
• In terms of colours, I would not divert much from the logo colours (and of course white and black). I would like the flyer to be quite white. Almost like fairy-tale white: the white horse, the white snow, the white of the stars, the white heaven. White could be the base colour. White means peace, tranquillity, calm contentment, a smile.
• And then use the other colours. The green of the mindfulness. The blue of the sky, the dreams. And the orange of the sun, the energy, the fire, the action. And maybe the black for text.
• Where it says the "the way out is in" it would be great to have a similar font to the one I attach (see file "Font_the_way_out_is_in".
• I would like this flyer to be a piece of art, in every possible way. Simple, beautiful, ease, light, peaceful, calm happy. Just like the Quiet Pathfinder Course and bright meadow Company that I am creating intends to be. The mission of this Program and Company is to be a designer, a painter (a Picasso) of happier and more fulfilling human lives.
• I am very much looking forward to seeing your proposal(s).

```html
<!DOCTYPE html>
<html lang="en">
<head>
<meta charset="utf-8">
<title>Quiet Pathfinder Course – Free Information Session</title>
<link rel="stylesheet" href="https://fonts.googleapis.com/css2?family=Montserrat:wght@300;400;600;700&family=Titan+One&display=swap">
<style>
  :root {
    --white: #ffffff;
    --orange: #f37122;
    --blue: #33a6d7;
    --green: #acd037;
    --ink: #1d1d1b;
    --text: #333333;
    --muted: #555555;
    --rule: #c9c9c9;
    --photo-top: #d9d9d9;
    --photo-bottom: #8f8f8f;
  }
  * { box-sizing: border-box; margin: 0; padding: 0; }
  html, body { width: 848px; height: 1200px; overflow: hidden; background: var(--white); }
  body { font-family: "Montserrat", Arial, sans-serif; color: var(--text); }
  .flyer { position: relative; width: 848px; height: 1200px; background: var(--white); overflow: hidden; }

  /* brand */
  .brand { position: absolute; top: 40px; left: 0; width: 848px; text-align: center; }
  .brand-mark { display: block; width: 70px; height: 70px; margin: 0 auto 10px; border-radius: 50%; background: var(--orange); }
  .brand-name { font-size: 25px; font-weight: 600; color: var(--blue); letter-spacing: 0.2px; line-height: 1; }
  .brand-tagline { margin-top: 7px; font-size: 7px; font-weight: 600; letter-spacing: 0.6px; text-transform: uppercase; color: var(--muted); }

  /* title */
  .title { position: absolute; top: 178px; left: 0; width: 848px; height: 205px; overflow: visible; }
  .title text { font-family: "Titan One", "Arial Black", sans-serif; text-anchor: middle; }
  .title .outer { fill: none; stroke: var(--blue); stroke-width: 13; stroke-linejoin: round; }
  .title .inner { fill: none; stroke: var(--white); stroke-width: 7; stroke-linejoin: round; }
  .title .fill { fill: var(--orange); }

  /* session box */
  .session { position: absolute; top: 416px; left: 181px; width: 486px; height: 116px; text-align: center; }
  .session-frame { position: absolute; inset: 0; }
  .session-heading { position: relative; padding-top: 18px; font-size: 28px; font-weight: 400; color: var(--ink); letter-spacing: 0.5px; line-height: 32px; }
  .session-details { position: relative; margin-top: 6px; font-size: 14.5px; font-weight: 300; color: var(--ink); line-height: 26px; }

  /* intro columns */
  .intro { position: absolute; top: 572px; left: 105px; width: 285px; font-size: 15.2px; font-weight: 300; line-height: 21.8px; color: var(--ink); }
  .audience { position: absolute; top: 572px; left: 443px; width: 300px; font-size: 15.2px; font-weight: 300; line-height: 21.8px; color: var(--ink); }
  .audience h2 { font-size: 16px; font-weight: 700; letter-spacing: 0.3px; line-height: 21.8px; }

  /* facilitator */
  .facilitator-photo { position: absolute; top: 767px; left: 86px; width: 154px; height: 209px; background: linear-gradient(180deg, var(--photo-top), var(--photo-bottom)); }
  .facilitator-name { position: absolute; top: 983px; left: 86px; width: 170px; }
  .facilitator-name strong { display: block; font-size: 15px; font-weight: 700; font-style: italic; color: var(--ink); line-height: 20px; }
  .facilitator-name span { display: block; font-size: 10.5px; font-weight: 300; line-height: 1.35; color: var(--ink); }
  .facilitator-bio { position: absolute; top: 758px; left: 266px; width: 520px; font-size: 14px; font-weight: 300; line-height: 24.6px; color: var(--ink); }
  .facilitator-link { position: absolute; top: 1057px; left: 266px; font-size: 15.5px; font-weight: 700; line-height: 22px; color: var(--ink); }

  /* footer */
  .contact { position: absolute; top: 1104px; left: 0; width: 848px; height: 96px; border-top: 1.5px solid var(--rule); }
  .contact-item { position: absolute; top: 26px; display: flex; align-items: center; gap: 10px; font-size: 14.5px; font-weight: 400; color: var(--ink); line-height: 22px; }
  .contact-email { left: 92px; }
  .contact-label { left: 306px; font-weight: 700; }
  .contact-phone { left: 534px; }
  .contact-icon { width: 22px; height: 22px; }
  .color-band { position: absolute; bottom: 0; left: 0; width: 848px; height: 20px; display: flex; }
  .band-blue { width: 627px; background: var(--blue); }
  .band-green { width: 143px; background: var(--green); }
  .band-orange { flex: 1; background: var(--orange); }
</style>
</head>
<body>
<main class="flyer">

  <header class="brand">
    <span class="brand-mark" aria-hidden="true"></span>
    <div class="brand-name">bright meadow</div>
    <div class="brand-tagline">Stillness, Craft and Venture for Bright Meadow</div>
  </header>

  <svg class="title" viewBox="0 0 848 205" role="heading" aria-level="1" aria-label="Quiet Pathfinder Course">
    <g font-size="88">
      <text class="outer" x="424" y="72">QUIET</text>
      <text class="inner" x="424" y="72">QUIET</text>
      <text class="fill" x="424" y="72">QUIET</text>
    </g>
    <g font-size="56">
      <text class="outer" x="424" y="128">PATHFINDER</text>
      <text class="inner" x="424" y="128">PATHFINDER</text>
      <text class="fill" x="424" y="128">PATHFINDER</text>
    </g>
    <g font-size="64">
      <text class="outer" x="424" y="192">COURSE</text>
      <text class="inner" x="424" y="192">COURSE</text>
      <text class="fill" x="424" y="192">COURSE</text>
    </g>
  </svg>

  <section class="session">
    <svg class="session-frame" viewBox="0 0 486 116" aria-hidden="true">
      <line x1="33" y1="1" x2="453" y2="1" stroke="#acd037" stroke-width="2"/>
      <line x1="33" y1="115" x2="453" y2="115" stroke="#acd037" stroke-width="2"/>
      <polyline points="14,9 1,9 1,92 14,92" fill="none" stroke="#33a6d7" stroke-width="2"/>
      <polyline points="472,9 485,9 485,92 472,92" fill="none" stroke="#33a6d7" stroke-width="2"/>
    </svg>
    <h2 class="session-heading">FREE INFORMATION SESSION</h2>
    <p class="session-details">Date : Thursday 5th September 2019 &nbsp;|&nbsp; Time : 19:30 to 21:00<br>Venue: Kona Coworking, C/ Almendro 42, Barcelona</p>
  </section>

  <p class="intro">The purpose of this free Information Session is to give you a real insight into the Quiet Pathfinder Course and how it can help you make the most of your professional and personal life.</p>

  <section class="audience">
    <h2>WHO CAN COME</h2>
    <p>Whether you come on your own, or with friends or family, you'll be warmly welcomed. The session will take place on Thursday the 5th September 2019, from 19:30 to 21:00, at KONA Coworking. Please see information below to get in contact or to book a seat.</p>
  </section>

  <div class="facilitator-photo" role="img" aria-label="Portrait photo of the facilitator"></div>
  <div class="facilitator-name">
    <strong>Dr Tomas Varela</strong>
    <span>Visiting Research Fellow<br>Harwell University</span>
  </div>
  <p class="facilitator-bio">Tomas joined the Harwell University School of Management as a Lecturer in Entrepreneurship in 2015. He completed his PhD in Entrepreneurship at Kelvin Business School in 2014, receiving the prestigious Society of Management's Larkin Doctoral Dissertation Award. He began his business career as a Production Engineer for Voltrix, and later as a Sales Engineer for Meridian Systems. After his MBA, he served as a Strategy Consultant for Douro Business School. Originally from Portugal, Tomas enjoys designing and launching new ideas, international communities, mindfulness retreats, and musical improvisation. He nurtures a close connection to Willow Hollow Mindfulness Centre, where he has practiced and volunteered over 9 months. He has a broad experience of sharing the benefits of mindfulness with others.</p>
  <p class="facilitator-link">More about the facilitator: www.tomasvarela.me</p>

  <footer class="contact">
    <div class="contact-item contact-email">
      <svg class="contact-icon" viewBox="0 0 22 22" aria-hidden="true">
        <circle cx="11" cy="11" r="11" fill="#33a6d7"/>
        <rect x="5.5" y="7" width="11" height="8" fill="none" stroke="#ffffff" stroke-width="1.3"/>
        <polyline points="5.5,7 11,11.5 16.5,7" fill="none" stroke="#ffffff" stroke-width="1.3"/>
      </svg>
      <span>Info@brightmeadow.io</span>
    </div>
    <div class="contact-item contact-label">Information &amp; Booking</div>
    <div class="contact-item contact-phone">
      <svg class="contact-icon" viewBox="0 0 22 22" aria-hidden="true">
        <circle cx="11" cy="11" r="11" fill="#33a6d7"/>
        <path d="M7.6 5.8c.5-.4 1.1-.3 1.4.2l1.1 1.8c.3.5.2 1-.2 1.3l-.8.6c.6 1.4 1.6 2.4 3 3l.6-.8c.3-.4.8-.5 1.3-.2l1.8 1.1c.5.3.6.9.2 1.4l-.8.9c-.6.6-1.5.8-2.3.5-3-1.2-5.2-3.4-6.4-6.4-.3-.8-.1-1.7.5-2.3z" fill="#ffffff"/>
      </svg>
      <span>Tel: +34 611 402 735</span>
    </div>
    <div class="color-band" aria-hidden="true">
      <span class="band-blue"></span><span class="band-green"></span><span class="band-orange"></span>
    </div>
  </footer>

</main>
</body>
</html>
```